Corvex Hiring Partners Business Cards

Business cards with logo design for a new recruiting company called "Corvex Hiring Partners"

incorporate RED & BLUE colors

Final design should reflect strength - clean, elegant design

Company name superimposed upon graphic (Greek Columns)

Please see attached Photos!!!

Industry/Entity Type

Business

Font styles to use
Decorative

Colors
ec2027
0555a3
85cae6

Requirements
Must have
• Must look very similar to attached design!!!

Want Company name superimposed upon graphic (Greek Columns)

Tag line at bottom must be included:
"Building Stronger Companies with Outstanding Talent"

```html
<!DOCTYPE html>
<html lang="en">
<head>
<meta charset="utf-8">
<title>Corvex Hiring Partners – Business Card</title>
<link rel="stylesheet" href="https://fonts.googleapis.com/css2?family=Questrial&family=Open+Sans:wght@700&display=swap">
<style>
  :root {
    --red: #ec2027;
    --blue: #0555a3;
    --sky: #85cae6;
    --ink: #3a3a3a;
    --icon: #555555;
    --card: #f4f5f6;
    --backdrop: #e3e5e8;
    --white: #ffffff;
  }
  * { margin: 0; padding: 0; box-sizing: border-box; }
  html, body { width: 1200px; height: 1000px; overflow: hidden; }
  body {
    background: var(--backdrop);
    font-family: "Questrial", "Century Gothic", sans-serif;
    position: relative;
  }
  .card {
    position: absolute;
    left: 100px; top: 214px;
    width: 1000px; height: 572px;
    background: linear-gradient(135deg, var(--white) 0%, var(--card) 100%);
    box-shadow: 0 6px 24px rgba(0,0,0,.15);
    overflow: hidden;
  }
  .top-stripe {
    position: absolute; left: 0; right: 0; top: 0;
    height: 14px; background: var(--sky);
  }
  .brand {
    position: absolute; left: 70px; top: 150px;
    display: flex; align-items: center; gap: 26px;
  }
  .brand-square {
    width: 130px; height: 130px; background: var(--blue); flex: none;
  }
  .brand-name {
    color: var(--blue);
    font-size: 46px; line-height: 1.08;
    font-weight: 400;
  }
  .divider {
    position: absolute; left: 500px; top: 90px;
    width: 5px; height: 340px; background: var(--red);
  }
  .contact {
    position: absolute; left: 550px; top: 130px;
    color: var(--ink);
  }
  .contact-name {
    color: var(--blue); font-size: 32px; margin-bottom: 34px; padding-left: 60px;
  }
  .contact-name strong { font-family: "Open Sans", sans-serif; font-weight: 700; }
  .contact-row {
    display: flex; align-items: center; gap: 26px;
    font-size: 28px; height: 62px;
  }
  .contact-row svg { width: 34px; height: 34px; flex: none; }
  .bottom-stripe {
    position: absolute; left: 0; right: 0; bottom: 82px;
    height: 10px; background: var(--sky);
  }
  .tagline-band {
    position: absolute; left: 0; right: 0; bottom: 0;
    height: 82px; background: var(--blue);
    display: flex; align-items: center; padding-left: 40px;
  }
  .tagline {
    color: var(--white);
    font-family: "Open Sans", sans-serif; font-weight: 700;
    font-size: 30px; white-space: nowrap;
  }
</style>
</head>
<body>
  <section class="card">
    <div class="top-stripe"></div>

    <div class="brand">
      <div class="brand-square"></div>
      <div class="brand-name">Corvex<br>Hiring<br>Partners</div>
    </div>

    <div class="divider"></div>

    <div class="contact">
      <p class="contact-name">Daniel R. <strong>Whitmore</strong></p>
      <div class="contact-row">
        <svg viewBox="0 0 24 24" aria-hidden="true"><rect x="7" y="3" width="10" height="18" rx="2" fill="none" stroke="#555" stroke-width="1.8"/><rect x="9" y="6" width="6" height="5" fill="#555"/><line x1="8" y1="1" x2="8" y2="3" stroke="#555" stroke-width="1.8"/></svg>
        <span>512.555.0147</span>
      </div>
      <div class="contact-row">
        <svg viewBox="0 0 24 24" aria-hidden="true"><rect x="2" y="6" width="20" height="14" fill="#555"/><path d="M2 6 L12 14 L22 6" fill="none" stroke="#fff" stroke-width="1.5"/></svg>
        <span>DWhitmore@CorvexHP.com</span>
      </div>
      <div class="contact-row">
        <svg viewBox="0 0 24 24" aria-hidden="true"><circle cx="12" cy="12" r="10" fill="#6a6a6a"/><path d="M5 9 Q9 7 10 11 Q12 14 9 17 M14 5 Q17 9 15 12 Q14 16 18 17" fill="none" stroke="#bbb" stroke-width="1.6"/></svg>
        <span>www. CorvexHP.com</span>
      </div>
    </div>

    <div class="bottom-stripe"></div>
    <div class="tagline-band">
      <p class="tagline">Building Stronger Companies with Outstanding Talent</p>
    </div>
  </section>
</body>
</html>
```